Social Media Templates for Fieldhouse Raffle Fund

We need a set of Square (1080 x 1080) social media posts.

My company works with sports clubs, helping them to raise money with a lottery.

I need a set of social media image that I can use to appeal to new Fieldhouse Raffle Fund to encourage them to start a lottery with us.

This landing page has worked very well for us https://fieldhouserafflefund.com/fieldhouse-raffle-fund/

THING THAT APPEAL TO CLUBS

No Setup Fees/Start for Free - (We don’t charge any registration fees, or setup fees so you can start raising money from the first draw.)

Start Straight Away - (A club can start raising money straight away.)

Sustainable Income - (The average player plays for 7 years)

Subscription Lottery - (once a player joins, they play until the choose to leave. A club doesn't have to sell tickets every draw to the same people)

All Administration Taken Care Of - (We do all the hard work, so they can focus on running their club.)

Unlimited Income - (There is no limit on the amount of money a club can raise: the more players, the more funds for the club.)

Fundraising reach - (Reach new fans)

50% of the sales is guaranteed profit

£25,000 jackpot - (a person could win £25,000 every week)

Price - (It costs just £1 per week to enter)

Help Your Club - (100% of the profit goes to the club who a player chooses to support)

You can see all the clubs we work with on www.fieldhouserafflefund.com

The images will also be used on Chatterwall. You can see some examples here https://www.chatterwall.com/FieldhouseRaffleFund/ (you may need a proxy to view this page as it is only viewable in the UK, so I have attached some screenshots)

You can find the Fieldhouse Raffle Fund Logo here https://www.logovault.com/winwellgroup/

Target Market(s)

People who are involved with amateur sports in United Kingdom

Industry/Entity Type

Gambling

Font styles to use
Sans Serif

Requirements
Must have
• My project must look great on social social media and encourage people to get in touch about starting a lottery with us.

Adobe Suite files must be provided

```html
<!DOCTYPE html>
<html lang="en">
<head>
<meta charset="utf-8">
<title>Fieldhouse Raffle Fund – No Setup Fees</title>
<link rel="stylesheet" href="https://fonts.googleapis.com/css2?family=Raleway:wght@400;800&display=swap">
<style>
  :root {
    --grass-dark: #1f6a22;
    --grass-mid: #3a8f2e;
    --grass-light: #5aa83a;
    --paper: #ffffff;
    --paper-shade: #eeeeee;
    --accent-orange: #e8730f;
    --brand-blue: #2a7fbb;
    --body-grey: #4a4a4a;
    --trophy-gold: #c9a227;
    --photo-red: #d8232a;
    --photo-turf: #3f7a4a;
  }
  html, body {
    margin: 0;
    padding: 0;
    width: 1200px;
    height: 1200px;
    overflow: hidden;
    background: #ffffff;
  }
  .post {
    position: relative;
    width: 1200px;
    height: 1200px;
    overflow: hidden;
    font-family: "Raleway", sans-serif;
  }
  .post-shapes {
    position: absolute;
    inset: 0;
  }
  .brand-name {
    position: absolute;
    left: 86px;
    top: 334px;
    width: 386px;
    height: 331px;
    display: flex;
    align-items: center;
    justify-content: center;
    text-align: center;
    margin: 0;
    font-family: "Raleway", sans-serif;
    font-weight: 800;
    font-size: 52px;
    line-height: 1.08;
    text-transform: uppercase;
    color: var(--brand-blue);
  }
  .headline {
    position: absolute;
    left: 78px;
    top: 776px;
    margin: 0;
    font-family: "Raleway", sans-serif;
    font-weight: 800;
    font-size: 71px;
    line-height: 88px;
    letter-spacing: 0.5px;
    color: var(--brand-blue);
    white-space: nowrap;
  }
  .body-copy {
    position: absolute;
    left: 78px;
    top: 960px;
    margin: 0;
    font-family: "Raleway", sans-serif;
    font-weight: 400;
    font-size: 29px;
    line-height: 38px;
    color: var(--body-grey);
    white-space: nowrap;
  }
</style>
</head>
<body>
<main class="post">
  <svg class="post-shapes" width="1200" height="1200" viewBox="0 0 1200 1200" xmlns="http://www.w3.org/2000/svg">
    <defs>
      <linearGradient id="grass-fill" x1="0" y1="0" x2="1" y2="1">
        <stop offset="0" stop-color="var(--grass-mid)"/>
        <stop offset="0.5" stop-color="var(--grass-dark)"/>
        <stop offset="1" stop-color="var(--grass-light)"/>
      </linearGradient>
      <linearGradient id="paper-fill" x1="0" y1="0" x2="0" y2="1">
        <stop offset="0.55" stop-color="var(--paper)"/>
        <stop offset="1" stop-color="var(--paper-shade)"/>
      </linearGradient>
      <linearGradient id="team-fill" x1="0" y1="0" x2="0" y2="1">
        <stop offset="0" stop-color="#2d5a33"/>
        <stop offset="0.25" stop-color="var(--photo-red)"/>
        <stop offset="0.75" stop-color="var(--photo-red)"/>
        <stop offset="1" stop-color="var(--photo-turf)"/>
      </linearGradient>
      <linearGradient id="trophy-fill" x1="0" y1="0" x2="1" y2="0">
        <stop offset="0" stop-color="#a8831a"/>
        <stop offset="0.5" stop-color="var(--trophy-gold)"/>
        <stop offset="1" stop-color="#8a6c14"/>
      </linearGradient>
    </defs>

    <rect class="grass-backdrop" x="0" y="0" width="1200" height="1200" fill="url(#grass-fill)" role="img" aria-label="Close-up of green artificial turf"/>

    <rect class="trophy-area" x="0" y="0" width="171" height="206" fill="url(#trophy-fill)" role="img" aria-label="Gold trophy cup"/>

    <circle class="team-photo" cx="963" cy="369" r="413" fill="url(#team-fill)" role="img" aria-label="Youth football team in red kits huddled on a pitch"/>
    <circle class="team-photo-ring" cx="963" cy="369" r="382" fill="none" stroke="#ffffff" stroke-width="2"/>

    <ellipse class="copy-panel" cx="292" cy="879" rx="552" ry="661" fill="url(#paper-fill)"/>
    <ellipse class="copy-panel-line" cx="292" cy="879" rx="528" ry="633" fill="none" stroke="var(--accent-orange)" stroke-width="2"/>
  </svg>

  <p class="brand-name">Fieldhouse<br>Raffle<br>Fund</p>

  <h1 class="headline">NO SETUP FEES/<br>START FOR FREE</h1>

  <p class="body-copy">We don’t charge any registration fees,<br>or setup fees so you canstart raising money<br>from the first draw.</p>
</main>
</body>
</html>
```